Defense Attorney Business Card Design Project/ Stationary

I am looking for a distinctive business card design for my solo law practice.
I practice criminal defense, both juvenile and adult, including DUI. I am a very experienced attorney with prior military experience. The design should convey a traditional, old school flair, but not be too stodgy or uptight. Some color. My logo should appear.
Updates

Project Deadline Extended Reason: I misunderstood how this project works and I was not prepared with my logo when this project ran the first time. Added Thursday, November 13, 2014

Project Deadline Extended
Reason: I was sent overseas on military duty last year, which interrupted this project. Thank you for your participation... I hope we can get this done this week! Thank you, Neil

Target Market(s)

Regular everyday people looking for strong, knowledgeable, authoritative representation while they are faced with criminal charges. Many have never been charged with a crime before. A reassuring air is therefore desired.

Industry/Entity Type

Business

Contact Information for Business Card

My information is:
Theodore M. Quill, Attorney at Law
785 Birch Avenue Suite 300
Oakland, California 94719
Tel: (510) 384-6125
Fax: (510) 391-7802
email: neilquilllaw@mailvine.example
web: www.neilquilllaw.example

Font styles to use
Serif
Sans Serif
Decorative

Colors
0255a3
ffffff

Requirements
Must have
• Sharp lines, bold elements. Conservative use of colors, such as deep blues, burgundy, grays for example.
• While my logo says "Theodore M. Quill", it should be modified to show "Theodore M. Quill".
Should not have
• Cliche imagery such as scales of justice, gavels, Statue of Liberty, etc.

```html
<!DOCTYPE html>
<html lang="en">
<head>
<meta charset="utf-8">
<title>Theodore M. Quill – Business Card</title>
<link href="https://fonts.googleapis.com/css2?family=Open+Sans:wght@400;600;700&display=swap" rel="stylesheet">
<style>
  :root {
    --backdrop: #2c2c2e;
    --card-top: #ffffff;
    --card-bottom: #e4e5e7;
    --navy: #0e3a57;
    --title-blue: #1f5f86;
    --ink: #3b3b3d;
    --pill-grey: #b4b5b8;
    --white: #ffffff;
  }
  * { margin: 0; padding: 0; box-sizing: border-box; }
  html, body {
    width: 1200px;
    height: 816px;
    overflow: hidden;
    background: var(--backdrop);
    font-family: "Open Sans", Arial, sans-serif;
  }
  .canvas {
    position: relative;
    width: 1200px;
    height: 816px;
  }
  .card {
    position: absolute;
    left: 100px;
    top: 123px;
    width: 1000px;
    height: 570px;
    border-radius: 44px;
    overflow: hidden;
    background: linear-gradient(160deg, var(--card-top) 0%, var(--card-top) 45%, var(--card-bottom) 100%);
  }
  .card-shapes {
    position: absolute;
    inset: 0;
  }
  .identity {
    position: absolute;
    left: 62px;
    top: 214px;
  }
  .identity .person-name {
    font-size: 31px;
    font-weight: 700;
    color: var(--ink);
    letter-spacing: 0.3px;
    text-transform: uppercase;
  }
  .identity .person-title {
    font-size: 22px;
    font-weight: 400;
    color: var(--title-blue);
    margin-top: 2px;
  }
  .contact-list {
    position: absolute;
    left: 62px;
    top: 330px;
    list-style: none;
    font-size: 19px;
    color: var(--ink);
  }
  .contact-list li {
    display: flex;
    align-items: center;
    gap: 12px;
    line-height: 28px;
  }
  .contact-list .address {
    font-weight: 700;
    align-items: flex-start;
    margin-bottom: 2px;
  }
  .contact-list .icon {
    width: 18px;
    height: 18px;
    flex: none;
    fill: var(--navy);
  }
  .contact-list .address .icon { margin-top: 5px; }
  .firm-mark {
    position: absolute;
    left: 540px;
    top: 158px;
    width: 440px;
    display: flex;
    align-items: center;
    justify-content: center;
    gap: 14px;
  }
  .firm-mark .dot {
    width: 20px;
    height: 20px;
    border-radius: 50%;
    background: var(--navy);
    flex: none;
  }
  .firm-mark .firm-name {
    font-size: 36px;
    font-weight: 600;
    color: var(--navy);
    letter-spacing: 0.5px;
    white-space: nowrap;
  }
  .website {
    position: absolute;
    left: 528px;
    top: 348px;
    font-size: 29px;
    color: var(--white);
    letter-spacing: 0.4px;
  }
</style>
</head>
<body>
<main class="canvas">
  <article class="card">
    <svg class="card-shapes" width="1000" height="570" viewBox="0 0 1000 570" aria-hidden="true">
      <rect class="website-pill" x="486" y="328" width="560" height="92" rx="42" fill="var(--pill-grey)"/>
      <path class="base-band" d="M0,468 H430 Q466,468 478,444 Q490,420 526,420 H1000 V570 H0 Z" fill="var(--navy)"/>
    </svg>

    <div class="firm-mark">
      <span class="dot"></span>
      <span class="firm-name">Theodore M. Quill</span>
    </div>

    <div class="website">www.neilquilllaw.example</div>

    <header class="identity">
      <h1 class="person-name">Theodore M. Quill</h1>
      <p class="person-title">Attorney at Law</p>
    </header>

    <ul class="contact-list">
      <li class="address">
        <svg class="icon" viewBox="0 0 24 24"><path d="M12 2a7 7 0 0 0-7 7c0 5.2 7 13 7 13s7-7.8 7-13a7 7 0 0 0-7-7zm0 9.5A2.5 2.5 0 1 1 12 6.5a2.5 2.5 0 0 1 0 5z"/></svg>
        <span>785 Birch Avenue Suite 300</span>
      </li>
      <li>
        <svg class="icon" viewBox="0 0 24 24"><path d="M6.6 10.8a15.1 15.1 0 0 0 6.6 6.6l2.2-2.2a1 1 0 0 1 1-.25 11.4 11.4 0 0 0 3.6.57 1 1 0 0 1 1 1V20a1 1 0 0 1-1 1A17 17 0 0 1 3 4a1 1 0 0 1 1-1h3.5a1 1 0 0 1 1 1c0 1.25.2 2.450.57 3.57a1 1 0 0 1-.25 1z"/></svg>
        <span>(510) 384-6125</span>
      </li>
      <li>
        <svg class="icon" viewBox="0 0 24 24"><path d="M6 3h9l3 3v4H6zM4 11h16a2 2 0 0 1 2 2v7H2v-7a2 2 0 0 1 2-2zm12 3v2h3v-2z"/></svg>
        <span>(510) 391-7802</span>
      </li>
      <li>
        <svg class="icon" viewBox="0 0 24 24"><path d="M2 5h20v14H2zm2 2v.5l8 5.5 8-5.5V7z"/></svg>
        <span>neilquilllaw@mailvine.example</span>
      </li>
    </ul>
  </article>
</main>
</body>
</html>
```